Business Performance Improvement Book Cover Design Project

We need a book cover design for a new company, based in Eastern Australia, called Brovanta Consulting. We advise clients on process improvement, continuous improvement and business performance improvement, especially in the manufacturing areas and Fast Moving Consumer Goods industries.
We have a written a book designed to demonstrate our very high calibre of knowledge and to use as a marketing tool for prospective clients. We hope to give it out at training seminars and as a comprehensive business card.

Title of the book is: A rounded method for Enterprise Results Advancement.
Subtitle: Shape a Steady Refinement method to fit your firm's character.
Author: by Gareth Polwyn
Back Cover: No need for a bar code in this edition. An important aspect is that we will distribute by hand. Text below for back page.

'For the experienced Business Performers, this book is designed to offer an insight into the advantages and an example of an approach to Business Improvement. It is not the only way but it is tried and tested in world class companies and it works. For those new to Continuous Improvement, it offers a helpful introduction to a holistic business improvement system, an overview of important success factors and pitfalls, recommendations on how to implement tools and methods and a quick guide to see when to use which tools. '

'Consultancies are one of many tools management teams can engage and management must make sure the consultants tailor their approach to suit its business needs and culture and not vice versa.'

End of text for back cover.

Business Performance Improvement is also known as or can include:
Continuous Improvement
Process Improvement
Lean Six Sigma
Operational Excellence
Total Productive Maintenance
Varmeco Output Method
Total Quality Management
Business Process Re engineering
Yield Compass
=
Brovanta Consulting

The book size is 175 x 240 mm and will need a 10-15mm bleed. The spine is not known at this stage exactly and will need to be updated once the printing is finished but I suggest a 10mm until I have the exact size.

Our company colours are Pantone 288, R0,G75,B141, C100,M79,Y17,K3. Attached are some other publications that give a sense of what we like to portray, Some words which might add to this are: professional, elegance, quality, sleek.
Updates

Reason: After receiving the designs, I realised that I needed to update the brief with more and better quality information for designers to work with.

Target Market(s)

people in the accounting and insolvency industries, production managers and CEOs, Chief Operating Officers, members of the executive team of large companies and GMs of small companies.

Industry/Entity Type

Marketing

Requirements
Must have
• Communicate an image that shows an improvement or increase of something.
Very professional and elegant
Emphasis on the words 'Business Performance Improvement' in the title, subtitle also important
Must appeal to a high-end of the market audience
Nice to have
• Recommendation for your cover to be gloss or matt in print
Image can be indirectly related to money but not specifically
Somehow that it matches or is not so different to the attached brochure
Should not have
• Not be too loud or commercial
Book jacket. WIll be printed as soft cover first run and hard cover 2nd run

```html
<!DOCTYPE html>
<html lang="en">
<head>
<meta charset="UTF-8">
<title>Brovanta Consulting – Book Cover Concept</title>
<link rel="stylesheet" href="https://fonts.googleapis.com/css2?family=Roboto+Condensed:wght@300;400&display=swap">
<style>
  :root {
    --page: #ffffff;
    --navy: #0a1f5e;
    --deep: #0b2a86;
    --bright: #0a4dff;
    --glow-light: #5fe0ff;
    --glow-mid: #2f8bf0;
    --glow-soft: #1d5fe0;
    --brand: #1538c8;
    --ink-light: #ffffff;
    --ink-soft: rgba(255,255,255,0.85);
  }
  * { margin: 0; padding: 0; box-sizing: border-box; }
  html, body {
    width: 1200px;
    height: 1000px;
    overflow: hidden;
    background: var(--page);
  }
  .canvas {
    position: relative;
    width: 1200px;
    height: 1000px;
    background: var(--page);
    font-family: "Roboto Condensed", "Arial Narrow", sans-serif;
  }
  .cover {
    position: absolute;
    left: 295px;
    top: 54px;
    width: 631px;
    height: 815px;
    overflow: hidden;
    background: linear-gradient(150deg,
      var(--navy) 0%,
      var(--deep) 22%,
      var(--bright) 45%,
      var(--bright) 52%,
      var(--deep) 72%,
      var(--navy) 100%);
  }
  .motif {
    position: absolute;
    border-radius: 50%;
  }
  .motif--top {
    left: 125px; top: -120px; width: 360px; height: 360px;
    background: radial-gradient(circle, var(--navy) 0 22%, var(--glow-light) 30%, var(--glow-mid) 55%, rgba(47,139,240,0.5) 75%, rgba(47,139,240,0) 100%);
  }
  .motif--right {
    left: 405px; top: 215px; width: 320px; height: 320px;
    background: radial-gradient(circle, var(--navy) 0 15%, var(--glow-mid) 25%, rgba(47,139,240,0.8) 55%, rgba(47,139,240,0.3) 85%, rgba(47,139,240,0) 100%);
  }
  .motif--lower {
    left: 265px; top: 526px; width: 280px; height: 280px;
    background: radial-gradient(circle, var(--navy) 0 14%, var(--glow-soft) 24%, rgba(29,95,224,0.7) 60%, rgba(29,95,224,0) 100%);
  }
  .motif--corner {
    left: 40px; top: 601px; width: 220px; height: 220px;
    background: radial-gradient(circle, var(--navy) 0 14%, rgba(29,95,224,0.6) 26%, rgba(29,95,224,0.35) 65%, rgba(29,95,224,0) 100%);
  }
  .book-title {
    position: absolute;
    left: 139px;
    top: 246px;
    width: 230px;
    color: var(--ink-light);
    font-weight: 400;
    font-size: 22px;
    line-height: 26px;
  }
  .values {
    position: absolute;
    left: 139px;
    top: 333px;
    list-style: none;
    color: var(--ink-light);
    font-weight: 400;
    font-size: 27px;
    line-height: 38px;
  }
  .book-subtitle {
    position: absolute;
    left: 139px;
    top: 496px;
    width: 220px;
    color: var(--ink-soft);
    font-weight: 300;
    font-size: 14px;
    line-height: 18px;
  }
  .book-author {
    position: absolute;
    left: 139px;
    top: 540px;
    color: var(--ink-light);
    font-weight: 400;
    font-size: 17px;
    line-height: 20px;
  }
  .brand {
    position: absolute;
    left: 665px;
    top: 884px;
    display: flex;
    align-items: center;
    gap: 12px;
    color: var(--brand);
  }
  .brand__dot {
    width: 46px;
    height: 46px;
    border-radius: 50%;
    background: var(--brand);
  }
  .brand__name {
    font-weight: 400;
    font-size: 26px;
    line-height: 1;
  }
</style>
</head>
<body>
  <main class="canvas">
    <section class="cover" aria-label="Book cover">
      <div class="motif motif--top" role="img" aria-label="Glowing radiating arrow rosette ornament"></div>
      <div class="motif motif--right" role="img" aria-label="Radiating arrow rosette ornament"></div>
      <div class="motif motif--lower" role="img" aria-label="Faint radiating arrow rosette ornament"></div>
      <div class="motif motif--corner" role="img" aria-label="Faint radiating arrow rosette ornament"></div>
      <h1 class="book-title">A rounded method for<br>Enterprise Results<br>Advancement</h1>
      <ul class="values">
        <li>Professional</li>
        <li>Elegance</li>
        <li>Quality</li>
        <li>Sleek</li>
      </ul>
      <p class="book-subtitle">Shape a Steady Refinement method to fit your firm's character</p>
      <p class="book-author">by Gareth Polwyn</p>
    </section>
    <div class="brand">
      <span class="brand__dot"></span>
      <span class="brand__name">Brovanta Consulting</span>
    </div>
  </main>
</body>
</html>
```